Quillmarsh Property Solutions need a business card design

Hello guys. We would need a business card design asap please.
We are a start up property investment business based in London UK specialised in buying, selling, managing and letting properties and helping distressed property owners.
The name of our Business is Quillmarsh, the logo symbolises the four fundamental elements of the world (earth, air, fire and water) and so it stands for strength, stability, longevity.
We would like the business card to communicate professionalism and reliability. Many many thanks indeed for your work.

Details:

1.) Rosalind Updike
Property Investor
Mobile: +44(0)7700123456
Email: rosalind.quillmarsh@mailbox-example.com

2.) Dominic Updike
Property Investor
Mobile: +44(0)7700987654
Email: dominic.quillmarsh@mailbox-example.com

```html
<!DOCTYPE html>
<html lang="en">
<head>
<meta charset="utf-8">
<title>Quillmarsh Property Solutions – Business Card</title>
<link href="https://fonts.googleapis.com/css2?family=Open+Sans:wght@400;600;700&display=swap" rel="stylesheet">
<style>
  :root{
    --backdrop:#8e8e8e;
    --card:#f4f4f4;
    --card-edge:#ffffff;
    --blue:#3d8ee8;
    --strip:#c9ccd0;
    --ink:#3a3a3a;
    --ink-soft:#555;
    --divider:#d8d8d8;
  }
  *{margin:0;padding:0;box-sizing:border-box}
  html,body{width:1200px;height:894px;overflow:hidden}
  body{
    background:radial-gradient(ellipse at 50% 40%,#a3a3a3,var(--backdrop));
    font-family:"Open Sans",Arial,sans-serif;
    position:relative;
  }
  .card{
    position:absolute;
    width:525px;height:300px;
    background:linear-gradient(160deg,var(--card-edge),var(--card));
    box-shadow:0 10px 30px rgba(0,0,0,.35);
    overflow:hidden;
  }
  .card--front{left:45px;top:297px}
  .card--back{left:630px;top:297px}
  .card__band{position:absolute;left:0;top:0;width:100%;height:100%}

  /* front */
  .contact{position:absolute;left:84px;top:46px;color:var(--ink);font-size:16px;line-height:27px;white-space:nowrap}
  .person{position:absolute;left:66px;top:212px;white-space:nowrap}
  .person__name{font-size:20px;font-weight:700;color:var(--ink)}
  .person__title{font-size:14px;color:var(--blue);margin-top:-2px}
  .divider{position:absolute;left:330px;top:70px;width:1px;height:200px;background:var(--divider)}
  .front-brand{position:absolute;left:330px;right:0;top:72px;text-align:center}
  .address{position:absolute;left:345px;top:186px;color:var(--ink-soft);font-size:13.5px;line-height:21px;white-space:nowrap}
  .website{position:absolute;left:345px;top:250px;color:var(--blue);font-size:12px;font-weight:600;letter-spacing:.8px;white-space:nowrap}

  /* brand lockup */
  .brand{display:inline-flex;align-items:center;gap:9px}
  .brand__mark{width:18px;height:18px;background:var(--blue)}
  .brand__name{font-weight:700;font-size:22px;color:var(--ink);letter-spacing:.5px}
  .back-brand{position:absolute;left:0;right:40px;top:128px;text-align:center}
</style>
</head>
<body>

<section class="card card--front" aria-label="Business card front">
  <svg class="card__band" viewBox="0 0 525 300" aria-hidden="true">
    <path d="M0 0H72V14Q72 30 56 34L52 35Q46 37 46 46V300H0Z" fill="var(--strip)"/>
    <path d="M0 0H62V12Q62 24 50 27L44 29Q36 32 36 42V300H0Z" fill="var(--blue)"/>
    <g fill="none" stroke="#fff" stroke-width="1.6" stroke-linejoin="round" stroke-linecap="round">
      <path d="M12 56q2-4 5-4l2 4-2 2q2 4 5 6l2-2 4 2q0 3-4 5q-8-2-12-13z"/>
      <rect x="13" y="80" width="10" height="17" rx="2"/>
      <path d="M17 94h2"/>
      <rect x="11" y="113" width="15" height="9" rx="1"/>
      <path d="M14 113v-5h9v5M14 122v3h9v-3"/>
      <rect x="11" y="140" width="15" height="11" rx="1"/>
      <path d="M11 141l7.5 6 7.5-6"/>
    </g>
  </svg>

  <div class="contact">
    <p>(+44) 7700 123456</p>
    <p>(+44) 7700 123456</p>
    <p>(+44) 7700 123456</p>
    <p>info@quillmarsh.example</p>
  </div>

  <div class="person">
    <p class="person__name">Rosalind Updike</p>
    <p class="person__title">President and CEO</p>
  </div>

  <div class="divider"></div>

  <div class="front-brand">
    <div class="brand"><span class="brand__mark"></span><span class="brand__name">Quillmarsh</span></div>
  </div>

  <p class="address">14 Fenwick Row, London<br>United Kingdom EC1A 9ZZ</p>
  <p class="website">www.quillmarsh.example</p>
</section>

<section class="card card--back" aria-label="Business card back">
  <svg class="card__band" viewBox="0 0 525 300" aria-hidden="true">
    <path d="M525 0V300H470V288Q470 276 482 272L486 270Q494 266 494 256V44Q494 34 486 30L482 28Q470 24 470 12V0Z" fill="var(--strip)"/>
    <path d="M525 0V300H482V290Q482 280 492 276L496 274Q504 270 504 260V40Q504 30 496 26L492 24Q482 20 482 10V0Z" fill="var(--blue)"/>
  </svg>
  <div class="back-brand">
    <div class="brand"><span class="brand__mark"></span><span class="brand__name">Quillmarsh</span></div>
  </div>
</section>

</body>
</html>
```